Marrowby Water Taxi and Transport Business Card

I need business cards for my new water taxi and freight transport business I have started here in Kodiak Alaska. Kodiak is a remote island in the middle of the gulf of Alaska. There are seven native villages around the island and Kodiak is the #2 fishing port in the United States. We also have the largest Coast Guard Base in the U.S. My company will be providing water taxi and freight transport logistics to the villages and many hunting and fishing lodges as well as remote properties around the island.

I would like a business card that isn't status quo, something that stands out, either in feel or appearance. I do like clean minimal designs but it needs to have the necessary contact info on it.

Target Market(s)

remote lodge / property owners, residents of the many villages around Kodiak and any one wanting to enjoy the great outdoors of Kodiak Alaska

Industry/Entity Type

Business

Contact Information for Business Card

I like clean simple designs that aren't cluttered but still provide the necessary information

Colors
0255a3
3277b5
33a4d5
9bcb3c
add136
fbed22
ffc214
f78f20
f37122

Requirements
Must have
• logo and contact info
• Captain Mason Elwick
• www.marrowbyferryline.com
• mason@marrowbyferryline.com

```html
<!DOCTYPE html>
<html lang="en">
<head>
<meta charset="utf-8">
<title>Marrowby Water Taxi and Transport – Business Card</title>
<link rel="stylesheet" href="https://fonts.googleapis.com/css2?family=Open+Sans:wght@400;600;700&display=swap">
<style>
  :root {
    --stage: #2e2e2e;
    --card: #0d0d0d;
    --card-edge: #1a1a1a;
    --brand-blue: #33a4d5;
    --brand-sun: #f78f20;
    --text-light: #f2f2f2;
    --divider: #3a3a3a;
  }
  * { box-sizing: border-box; margin: 0; padding: 0; }
  html, body {
    width: 1200px; height: 900px; overflow: hidden;
    background: var(--stage);
    font-family: "Open Sans", Arial, sans-serif;
  }
  .stage {
    width: 1200px; height: 900px;
    display: flex; align-items: center; justify-content: center;
    gap: 48px;
  }
  .card {
    width: 525px; height: 300px;
    background: var(--card);
    border: 1px solid var(--card-edge);
    border-radius: 22px;
    box-shadow: 0 18px 40px rgba(0,0,0,.45);
    position: relative;
  }
  .brand-mark {
    width: 34px; height: 34px;
    border-radius: 50%;
    background: var(--brand-sun);
    margin: 0 auto 14px;
  }
  /* contact side */
  .card--contact { display: flex; align-items: center; }
  .card__brand {
    width: 240px; height: 100%;
    display: flex; flex-direction: column; align-items: center; justify-content: center;
    padding: 30px 24px 0;
  }
  .brand-name {
    color: var(--brand-blue);
    font-weight: 700;
    font-size: 20px;
    line-height: 1.2;
    text-align: center;
  }
  .card__divider {
    width: 1px; height: 120px;
    background: var(--divider);
  }
  .card__details { padding-left: 26px; }
  .person-name {
    color: var(--brand-blue);
    font-weight: 600;
    font-size: 19px;
    margin-bottom: 22px;
  }
  .contact-line {
    display: flex; align-items: center; gap: 10px;
    color: var(--text-light);
    font-size: 13.5px;
    line-height: 1.9;
  }
  .contact-line svg { width: 12px; height: 12px; flex: none; }
  /* logo side */
  .card--logo {
    display: flex; flex-direction: column; align-items: center; justify-content: center;
  }
  .card--logo .brand-mark { width: 44px; height: 44px; margin-bottom: 18px; }
  .logo-name {
    color: var(--brand-blue);
    font-weight: 700;
    font-size: 28px;
    line-height: 1.2;
    text-align: center;
    max-width: 360px;
  }
</style>
</head>
<body>
<main class="stage">
  <section class="card card--contact" aria-label="Business card, contact side">
    <div class="card__brand">
      <div class="brand-mark" aria-hidden="true"></div>
      <p class="brand-name">Marrowby Water Taxi and Transport</p>
    </div>
    <div class="card__divider"></div>
    <div class="card__details">
      <h1 class="person-name">Captain Mason Elwick</h1>
      <p class="contact-line">
        <svg viewBox="0 0 12 12" aria-hidden="true"><rect x="0.5" y="2" width="11" height="8" rx="1" fill="var(--brand-blue)"/><path d="M1 2.8 6 6.6 11 2.8" stroke="var(--card)" stroke-width="1" fill="none"/></svg>
        mason@marrowbyferryline.com
      </p>
      <p class="contact-line">
        <svg viewBox="0 0 12 12" aria-hidden="true"><path d="M5 7 7 5M4.2 5.6 2.6 7.2a1.8 1.8 0 0 0 2.5 2.5L6.7 8.1M7.8 6.4 9.4 4.8a1.8 1.8 0 0 0-2.5-2.5L5.3 3.9" stroke="var(--brand-blue)" stroke-width="1.3" fill="none" stroke-linecap="round"/></svg>
        www.marrowbyferryline.com
      </p>
    </div>
  </section>

  <section class="card card--logo" aria-label="Business card, logo side">
    <div class="brand-mark" aria-hidden="true"></div>
    <p class="logo-name">Marrowby Water Taxi and Transport</p>
  </section>
</main>
</body>
</html>
```